Computer consultant website

Plimvex Software is a newly started computer consulting company. It's a small one-man company that provides mostly Android applications but also websites in collaboration with designers. I'm running this company on the side of full time university studies.

I'm in need of a website which will function as:
Primarily - I'll direct potential clients to the page so they can read about the company, what i offer and past work.
Secondarily - Making my company visible through the web and maybe getting new clients.

The final design should look modern, clean and professional.

Pages that will be in the final website are (Note that it's not the exact titles as the page will not be in english):
* About
* Services (what Plimvex offers)
* Portfolio/work
* Short news (like ArtHivers "News and press")
* Contact.

Inspiration
http://www.arthiver.example/design/87836
http://www.brookwellstudio.example/
http://www.arthiver.example/design/845881
http://www.arthiver.example/design/1369424 - Lighter design, however a bit cluttered.

No programming code is needed delivered at all. Focus on designing rather then coding.

If you have any questions, do not hesitate to send me a message.

Target Market(s)

Non-technical entrepreneurs and small companies.

Industry/Entity Type

University

Requirements
Must have
• Must have my company logo (see attachment).

Must in any way use both colors from my logo.

A way to logically rearrange content to fit smaller screens. I will implement this design so that it can be pleasantly viewed on mobile devices. You don't necessarily need to provide exactly how the design would look on mobile devices.

I need the following types of page designs:
* Landing page
* Content page
* Portfolio/work (with accompanying inside/clicked) page

Landing/start page must in any way include at least the information:
* Shorter version of "About Plimvex"
* At least 1 most recent portfolio/work entry
* At least 1 most recent news entry
* Services that Plimvex offers.
Nice to have
• -
Should not have
• Testimonials or newsletter.

```html
<!DOCTYPE html>
<html lang="en">
<head>
<meta charset="utf-8">
<title>Plimvex – Computer Consulting</title>
<link href="https://fonts.googleapis.com/css2?family=Open+Sans:wght@300;400;600;700&display=swap" rel="stylesheet">
<style>
:root{
  --blue:#1f6fe8;
  --blue-dark:#0f4fb8;
  --ink:#222222;
  --text:#555555;
  --nav:#222222;
  --header-bg:#f2f2f2;
  --panel:#f1f1f1;
  --rule:#dcdcdc;
  --footer:#262626;
  --footer-text:#cfcfcf;
}
*{margin:0;padding:0;box-sizing:border-box}
html,body{width:1120px;height:1200px;overflow:hidden}
body{position:relative;background:#fff;font-family:'Open Sans',Arial,sans-serif;color:var(--text)}
a{color:var(--blue)}
.topnav{position:absolute;left:0;top:0;width:1120px;height:48px;background:var(--nav);border-top:3px solid var(--blue)}
.topnav .active-bar{position:absolute;left:154px;top:-3px;width:68px;height:3px;background:var(--nav)}
.topnav a{position:absolute;top:13px;font-size:14.5px;color:#fff;text-decoration:none}
.topnav a.active{color:var(--blue)}
.masthead{position:absolute;left:0;top:48px;width:1120px;height:110px;background:var(--header-bg);border-bottom:1px solid var(--rule)}
.brand{position:absolute;left:164px;top:22px;display:flex;align-items:center;gap:14px}
.brand-dot{width:64px;height:64px;border-radius:50%;background:var(--blue)}
.brand-name{font-size:46px;font-weight:600;color:#333;letter-spacing:-1px}
.consult{position:absolute;right:164px;top:28px;display:flex;gap:8px;align-items:center}
.consult-label{font-size:19px;color:var(--blue);line-height:1.1}
.consult-number{font-size:23px;font-weight:700;color:var(--ink);line-height:1.1}
.hero{position:absolute;left:0;top:158px;width:1120px;height:334px;background:linear-gradient(90deg,#f3f4f6 0%,#e6ebf1 60%,#dfe5ec 100%);border-bottom:1px solid var(--rule)}
.hero-title{position:absolute;left:167px;top:108px;font-size:40px;font-weight:300;line-height:39px;color:var(--ink)}
.hero-title em{font-style:normal;color:var(--blue)}
.hero-btn{position:absolute;left:166px;top:208px;width:187px;height:46px;background:linear-gradient(#555,#1e1e1e);border-radius:2px;color:#fff;font-weight:700;font-size:14px;line-height:46px;text-align:center}
.showcase{position:absolute;left:472px;top:194px;width:544px;height:344px;border-radius:14px 14px 40px 40px;background:linear-gradient(#e9e9e9,#c6c6c6)}
.arrow{position:absolute;top:330px;width:32px;height:32px;border-radius:50%;background:#fff;box-shadow:0 1px 4px rgba(0,0,0,.3)}
.main-col{position:absolute;left:167px;top:568px;width:510px}
h2{font-weight:400;color:var(--ink)}
.why h2{font-size:24px}
.sub{font-size:11.5px;font-weight:700;color:var(--blue);margin:2px 0 0 3px}
.body{font-size:11.6px;line-height:17.6px;margin-left:3px}
.more{display:block;font-size:11.5px;margin:9px 0 0 3px}
.news{position:absolute;left:170px;top:808px;width:510px}
.news h2{font-size:19px}
.news-item{display:flex;gap:34px;margin-top:10px}
.client-mark{width:90px;height:38px;border-radius:6px;background:var(--blue-dark);color:#fff;font-size:16px;font-weight:600;line-height:38px;text-align:center;flex:none}
.news-title{font-size:19px;color:var(--blue);margin-top:-2px}
.news-meta{font-size:9.5px;margin:1px 0 12px 2px}
.services{position:absolute;left:718px;top:585px;width:236px;height:387px;background:var(--panel);box-shadow:0 1px 3px rgba(0,0,0,.2)}
.services-head{height:52px;background:linear-gradient(var(--blue),var(--blue-dark));color:#fff;font-size:19px;font-weight:600;text-align:center;line-height:52px}
.service{height:83.5px;display:flex;align-items:center;gap:16px;padding-left:14px;border-bottom:1px solid var(--rule)}
.service:last-child{border-bottom:none}
.service-icon{width:60px;height:60px;border-radius:50% 50% 50% 0;background:#d0d0d0;display:flex;align-items:center;justify-content:center;flex:none}
.service-name{font-size:17px;line-height:20px;color:var(--blue);font-weight:400}
.footer{position:absolute;left:0;top:1072px;width:1120px;height:128px;background:var(--footer);color:var(--footer-text)}
.footer-nav a{position:absolute;top:39px;font-size:11.5px;color:#fff;text-decoration:none}
.copyright{position:absolute;left:175px;top:68px;font-size:11.5px}
.keep{position:absolute;left:730px;top:30px;width:180px;text-align:center;font-size:11px;color:#fff}
.keep::before,.keep::after{content:"";position:absolute;top:8px;width:40px;height:1px;background:#555}
.keep::before{left:0}.keep::after{right:0}
.social{position:absolute;left:728px;top:47px;display:flex;gap:5px}
.social span{width:32px;height:32px;border-radius:50%;background:#9a9a9a}
.call{position:absolute;left:758px;top:91px;font-size:11.5px;color:#6aa3ff}
</style>
</head>
<body>
<nav class="topnav">
  <div class="active-bar"></div>
  <a class="active" style="left:170px">Home</a>
  <a style="left:241px">About</a>
  <a style="left:315px">Services</a>
  <a style="left:400px">Works</a>
  <a style="left:472px">News</a>
  <a style="left:539px">Contact</a>
</nav>

<header class="masthead">
  <div class="brand"><div class="brand-dot"></div><div class="brand-name">plimvex</div></div>
  <div class="consult">
    <svg width="16" height="38" viewBox="0 0 16 38"><rect x="1" y="1" width="14" height="36" rx="2" fill="none" stroke="#666" stroke-width="2"/><rect x="4" y="5" width="8" height="12" fill="#666"/><g fill="#666"><rect x="4" y="21" width="3" height="3"/><rect x="9" y="21" width="3" height="3"/><rect x="4" y="27" width="3" height="3"/><rect x="9" y="27" width="3" height="3"/></g></svg>
    <div><div class="consult-label">Free Consultancy</div><div class="consult-number">010 55 2 4417</div></div>
  </div>
</header>

<section class="hero">
  <h1 class="hero-title"><span>WE ASSURE </span><em>YOU</em><br><span>QUALITY </span><em>WORK</em></h1>
  <div class="hero-btn">VISIT ALL OUR WORKS</div>
</section>
<div class="showcase" role="img" aria-label="Laptop displaying the Plimvex website homepage"></div>
<div class="arrow" style="left:518px"><svg width="32" height="32"><path d="M18 10l-6 6 6 6" stroke="#111" stroke-width="3" fill="none"/></svg></div>
<div class="arrow" style="left:936px"><svg width="32" height="32"><path d="M14 10l6 6-6 6" stroke="#111" stroke-width="3" fill="none"/></svg></div>

<section class="main-col why">
  <h2>Why should you choose us</h2>
  <p class="sub">consectetur adipiscing elit</p>
  <p class="body">Aenean metus mauris, auctor eget interdum id, imperdiet a lorem. Proin vitae elit ante, sit amet sollicitudin eros. Lorem ipsum dolor sit amet, consectetur adipiscing elit. Nam neque mauris, eleifend eget vestibulum non, accumsan non diam. Nulla risus mi, tincidunt sit amet auctor a, lobortis non eros.</p>
  <p class="sub" style="margin-top:17px">Nunc viverra fringilla arcu aliquam rutrum</p>
  <p class="body">Cras fringilla elit nunc, eget vulputate odio. Fusce semper nibh eu tellus facilisis ut porttitor urna auctor. Aenean luctus molestie ante non porta. Morbi sollicitudin pretium dolor. Cras gravida</p>
  <a class="more" href="#">Explore More About us</a>
</section>

<section class="news">
  <h2>Current News</h2>
  <div class="news-item">
    <div class="client-mark">Nestora</div>
    <div>
      <h3 class="news-title" style="font-weight:400">Cum sociis natoque penatibus et magnis dis</h3>
      <p class="news-meta">27th February 2012 | Nestora</p>
      <p class="body">Cras fringilla elit nunc, eget vulputate odio. Fusce semper nibh eu tellus facilisis ut porttitor urna auctor. Aenean luctus molestie ante non porta. Morbi sollicitudin pretium dolor. Cras gravida lobortis eleifend. Etiam auctor, orci eu molestie vestibulum, mi enim faucibus diam, quis interdum lectus purus a elit.</p>
      <a class="more" href="#" style="margin-top:13px">Read More News</a>
    </div>
  </div>
</section>

<aside class="services">
  <div class="services-head">Services We Offer</div>
  <div class="service"><div class="service-icon"><svg width="30" height="30"><rect x="6" y="11" width="18" height="14" rx="2" fill="#555"/><path d="M6 10a9 8 0 0118 0z" fill="#555"/></svg></div><div class="service-name">Android App<br>Development</div></div>
  <div class="service"><div class="service-icon"><svg width="30" height="30"><rect x="7" y="6" width="16" height="13" fill="none" stroke="#555" stroke-width="3"/><rect x="4" y="20" width="22" height="4" fill="#555"/></svg></div><div class="service-name">Web App<br>Development</div></div>
  <div class="service"><div class="service-icon"><svg width="30" height="30"><circle cx="12" cy="12" r="8" fill="none" stroke="#555" stroke-width="3"/><path d="M18 18l8 8" stroke="#555" stroke-width="4"/></svg></div><div class="service-name">Search Engine<br>Optimization</div></div>
  <div class="service"><div class="service-icon"><svg width="30" height="30"><path d="M25 5L11 19l-2-2L23 3z" fill="#555"/><path d="M9 20l-4 6 6-4z" fill="#555"/></svg></div><div class="service-name">User Experience<br>Design</div></div>
</aside>

<footer class="footer">
  <div class="footer-nav">
    <a style="left:175px">Home</a><a style="left:230px">About</a><a style="left:288px">Services</a><a style="left:354px">Works</a><a style="left:410px">News</a><a style="left:462px">Contact</a>
  </div>
  <p class="copyright">Copyright © 2013 Plimvex. All rights reserved | Terms and Conditions | Privacy Policy</p>
  <div class="keep">KEEP IN TOUCH</div>
  <div class="social"><span></span><span></span><span></span><span></span><span></span></div>
  <div class="call">Call us at &nbsp;010 552 4417</div>
</footer>
</body>
</html>
```